Insurance Agency website design for Brellow Cover Insurance, LP

Build a website for Brellow Cover Insurance, LP which sells Homeowners, Auto, Renters, Condo, Flood, Disability, Life, Umbrella, and health insurance. We need the coolest insurance agency website out there to get quotes, contact us, or get additional information. Please list the following insurance companies we work with: Varnix, Ostle, Meridale Mutual, Quillor, Dunmarrow, KGZ, and Pellwick.

Make a design similar to https://www.fernagentry.com/

Selling personal insurance policies

```html
<!DOCTYPE html>
<html lang="en">
<head>
<meta charset="utf-8">
<title>Brellow Cover Insurance</title>
<link href="https://fonts.googleapis.com/css2?family=Montserrat:wght@400;500;600;700&display=swap" rel="stylesheet">
<style>
:root{
  --navy:#0c2c77;
  --blue:#143e8f;
  --footer:#0f4a9a;
  --green:#8bc34a;
  --green-dark:#6fa82f;
  --ink:#1a1a2e;
  --muted:#6b6f7a;
  --soft:#f2f4f7;
  --white:#ffffff;
  --star:#f6a623;
}
*{box-sizing:border-box;margin:0;padding:0}
html,body{width:1200px;height:4552px;overflow:hidden}
body{position:relative;font-family:'Montserrat',sans-serif;color:var(--ink);background:var(--white)}
.abs{position:absolute}
.btn{position:absolute;display:flex;align-items:center;justify-content:center;font-size:14px;font-weight:500;border-radius:3px;color:var(--white)}
.btn-navy{background:var(--navy)}
.btn-green{background:var(--green)}
.eyebrow{position:absolute;font-size:11px;font-weight:600;letter-spacing:1.2px;color:var(--green);text-transform:uppercase}
.heading{position:absolute;font-weight:700;color:var(--blue)}
.rule{position:absolute;height:3px;width:62px;background:var(--green)}
.center{left:0;width:1200px;text-align:center}

/* top bar & nav */
.social-ring{position:absolute;top:11px;width:20px;height:20px;border:1px solid #333;border-radius:50%}
.topinfo{position:absolute;top:12px;font-size:13px;display:flex;align-items:center;gap:8px}
.topinfo .dot{width:19px;height:19px;border:1px solid #333;border-radius:50%;display:flex;align-items:center;justify-content:center}
.brand{position:absolute;left:141px;top:62px;font-size:20px;font-weight:700;letter-spacing:.2px}
.nav a{position:absolute;top:66px;font-size:13px;font-weight:500;color:var(--ink);text-decoration:none}

/* hero */
.hero{position:absolute;left:0;top:0;width:1200px;height:578px;background:linear-gradient(180deg,#eef2fb 0%,#e4eaf5 60%,#d9d2c8 100%);z-index:-1}
.hero-photo{position:absolute;left:565px;top:132px;width:635px;height:446px;background:linear-gradient(135deg,#c9cfd8 0%,#8f98a6 45%,#3c4a66 100%)}
.hero-desk{position:absolute;left:0;top:495px;width:565px;height:83px;background:linear-gradient(180deg,#b6a898,#8e7f70)}
.hero h1{position:absolute;left:141px;top:219px;font-size:52px;line-height:59px;font-weight:700;color:#222}
.hero p{position:absolute;left:141px;top:342px;font-size:16px;line-height:27px;color:#222}

/* features */
.features{position:absolute;left:0;top:578px;width:1200px;height:212px;background:var(--navy);overflow:hidden}
.feature{position:absolute;top:40px;width:200px;text-align:center;color:var(--white);font-size:16px;line-height:20px}
.feature .ring{width:86px;height:86px;margin:0 auto 20px;border-radius:50%;background:var(--white);border:4px solid #d9e1f2;display:flex;align-items:center;justify-content:center}

/* services */
.card{position:absolute;width:247px;text-align:center;padding-top:22px}
.card.active{background:var(--white);box-shadow:0 4px 18px rgba(0,0,0,.12);height:227px}
.card .icon{width:54px;height:54px;margin:0 auto;border:1px solid #dde2ea;border-radius:3px;display:flex;align-items:center;justify-content:center}
.card h3{font-size:16px;font-weight:600;margin:22px 0 13px}
.card.active h3{color:var(--green)}
.card p{font-size:11px;line-height:19px;color:var(--muted);padding:0 18px}

/* about */
.about{position:absolute;left:0;top:1599px;width:1200px;height:597px;background:var(--soft)}
.photo{position:absolute;border-radius:4px}
.about p{position:absolute;left:615px;width:430px;font-size:11px;line-height:20px;color:#555}

/* partners */
.partners{position:absolute;left:0;top:2196px;width:1200px;height:313px;background:linear-gradient(180deg,#2b5aa6,#1c4a98);overflow:hidden}
.logo-tile{position:absolute;top:188px;width:186px;height:54px;background:var(--white);display:flex;align-items:center;justify-content:center;font-size:17px;font-weight:600;color:var(--navy)}

/* testimonials */
.quote-card{position:absolute;top:2734px;width:445px;height:226px;background:var(--white);border-radius:8px;box-shadow:0 3px 16px rgba(0,0,0,.08)}
.quote-card .mark{position:absolute;left:20px;top:-4px;font-size:72px;line-height:72px;font-weight:700;color:#c7d0e0}
.quote-card p{position:absolute;left:28px;top:42px;width:390px;text-align:center;font-size:11px;line-height:23px;color:#555}
.quote-card .avatar{position:absolute;top:146px;width:54px;height:54px;border-radius:50%;background:linear-gradient(135deg,#c9a88c,#6b5444)}
.quote-card .who{position:absolute;top:152px;font-size:15px;font-weight:600;color:var(--blue)}
.quote-card .stars{position:absolute;top:174px;color:var(--star);font-size:17px;letter-spacing:2px}
.arrow{position:absolute;top:2832px;width:30px;height:30px;border-radius:50%;display:flex;align-items:center;justify-content:center}
.pager span{position:absolute;top:3008px;width:7px;height:7px;border-radius:50%;background:#c8ccd4}

/* contact */
.contact{position:absolute;left:0;top:3110px;width:1200px;height:618px;background:var(--soft)}
.field{position:absolute;background:var(--white);border:1px solid #d5d9e0;border-radius:3px;font-size:11px;color:#888;padding:13px 14px}

/* cta & footer */
.footer{position:absolute;left:0;top:3958px;width:1200px;height:594px;background:var(--footer)}
.cta{position:absolute;left:141px;top:3820px;width:917px;height:281px;background:var(--green);border-radius:14px;text-align:center;color:var(--white)}
.cta h2{position:absolute;left:0;width:100%;top:58px;font-size:29px;font-weight:700}
.cta p{position:absolute;left:110px;width:697px;top:110px;font-size:12px;line-height:22px}
.fsoc{position:absolute;top:4172px;width:35px;height:35px;border-radius:50%}
.fcol{position:absolute;top:4322px;width:260px;text-align:center;color:var(--white)}
.fcol h4{font-size:14px;font-weight:600;margin:12px 0 12px}
.fcol p{font-size:12px;line-height:22px;color:#dbe4f3}
.vline{position:absolute;top:4324px;width:1px;height:115px;background:rgba(255,255,255,.25)}
</style>
</head>
<body>

<!-- Hero -->
<div class="hero">
  <div class="hero-photo" role="img" aria-label="Photo of three colleagues reviewing an insurance plan on a laptop"></div>
  <div class="hero-desk" role="img" aria-label="Wooden desk with a small potted plant"></div>
  <h1>PROTECT WHAT<br>MATTERS MOST</h1>
  <p>Comprehensive insurance solutions for your<br>home, vehicle, health, and loved ones</p>
</div>
<a class="btn btn-navy" style="left:141px;top:412px;width:126px;height:40px">Get a Quote</a>

<!-- Top bar -->
<div class="social-ring" style="left:141px" aria-label="Social profile"></div>
<div class="social-ring" style="left:168px" aria-label="Social profile"></div>
<div class="social-ring" style="left:195px" aria-label="Social profile"></div>
<div class="social-ring" style="left:222px" aria-label="Social profile"></div>
<div class="topinfo" style="left:686px">
  <span class="dot"><svg width="10" height="10" viewBox="0 0 24 24"><path d="M6.6 10.8a15 15 0 006.6 6.6l2.2-2.2c.3-.3.7-.4 1-.2 1.1.4 2.3.6 3.6.6.6 0 1 .4 1 1V20c0 .6-.4 1-1 1C10.6 21 3 13.4 3 4c0-.6.4-1 1-1h3.5c.6 0 1 .4 1 1 0 1.3.2 2.5.6 3.6.1.3 0 .7-.2 1z" fill="#222"/></svg></span>(555) 214-0398
</div>
<div class="topinfo" style="left:827px">
  <span class="dot"><svg width="10" height="10" viewBox="0 0 24 24"><path d="M3 5h18v14H3z" fill="#222"/><path d="M3 5l9 7 9-7" stroke="#fff" stroke-width="2" fill="none"/></svg></span>info@BrellowCover.com
</div>

<div class="brand">BRELLOW COVER INSURANCE</div>
<nav class="nav">
  <a style="left:535px">Home</a>
  <a style="left:602px">About Us</a>
  <a style="left:691px">Insurance Types <svg width="10" height="8" viewBox="0 0 10 8"><path d="M1 2l4 4 4-4" stroke="#222" fill="none" stroke-width="1.4"/></svg></a>
  <a style="left:839px">Contact Us</a>
</nav>
<a class="btn btn-navy" style="left:931px;top:53px;width:127px;height:41px">Get a Quote</a>

<!-- Features band -->
<section class="features">
  <svg class="abs" style="left:0;top:0" width="1200" height="212"><polygon points="0,0 132,0 0,180" fill="#4a9e1c"/><polygon points="1200,100 1200,212 1058,212" fill="#4a9e1c"/></svg>
  <div class="feature" style="left:170px"><div class="ring"><svg width="40" height="40" viewBox="0 0 40 40"><rect x="9" y="5" width="22" height="30" rx="2" fill="none" stroke="#0c2c77" stroke-width="2"/><path d="M13 12h14M13 17h14M13 22h9" stroke="#0c2c77" stroke-width="2"/><circle cx="27" cy="29" r="5" fill="#0c2c77"/></svg></div>Insurance<br>Policies</div>
  <div class="feature" style="left:381px"><div class="ring"><svg width="40" height="40" viewBox="0 0 40 40"><path d="M20 6l4.2 8.6 9.5 1.4-6.9 6.7 1.6 9.4L20 27.6l-8.4 4.5 1.6-9.4-6.9-6.7 9.5-1.4z" fill="none" stroke="#0c2c77" stroke-width="2"/></svg></div>1000+ Happy<br>Clients</div>
  <div class="feature" style="left:600px"><div class="ring"><svg width="40" height="40" viewBox="0 0 40 40"><path d="M9 21a11 11 0 0122 0" fill="none" stroke="#0c2c77" stroke-width="2.4"/><rect x="6" y="20" width="6" height="9" rx="2" fill="#0c2c77"/><rect x="28" y="20" width="6" height="9" rx="2" fill="#0c2c77"/><path d="M31 29q0 5-7 5" fill="none" stroke="#0c2c77" stroke-width="2"/></svg></div>Professional<br>Support</div>
  <div class="feature" style="left:817px"><div class="ring"><svg width="40" height="40" viewBox="0 0 40 40"><circle cx="20" cy="20" r="6" fill="none" stroke="#0c2c77" stroke-width="2.4"/><circle cx="20" cy="20" r="12" fill="none" stroke="#0c2c77" stroke-width="2.4" stroke-dasharray="5 3"/></svg></div>Free Lifetime<br>Updates</div>
</section>

<!-- Services -->
<div class="eyebrow center" style="top:842px">Our Insurances</div>
<h2 class="heading center" style="top:868px;font-size:29px">Our Various Insurance Solutions</h2>
<div class="rule" style="left:569px;top:914px"></div>

<div class="card active" style="left:107px;top:960px"><div class="icon"><svg width="30" height="30" viewBox="0 0 30 30"><path d="M4 15L15 5l11 10" stroke="#0c2c77" stroke-width="2.4" fill="none"/><path d="M8 13v12h14V13" fill="#0c2c77"/></svg></div><h3>Homeowners</h3><p>Protect your home and belongings from damage, theft, or disaster with comprehensive homeowners coverage.</p></div>
<div class="card" style="left:374px;top:960px"><div class="icon"><svg width="30" height="30" viewBox="0 0 30 30"><path d="M5 16l3-7h14l3 7v7H5z" fill="#0c2c77"/><circle cx="10" cy="19" r="1.8" fill="#fff"/><circle cx="20" cy="19" r="1.8" fill="#fff"/></svg></div><h3>Auto Insurance</h3><p>Safeguard your vehicle against accidents, theft, or damage, ensuring you're covered on the road.</p></div>
<div class="card" style="left:621px;top:960px"><div class="icon"><svg width="30" height="30" viewBox="0 0 30 30"><path d="M4 13L15 5l11 8" stroke="#0c2c77" stroke-width="2.4" fill="none"/><rect x="7" y="13" width="16" height="12" fill="#0c2c77"/><rect x="10" y="16" width="4" height="4" fill="#fff"/><rect x="16" y="16" width="4" height="4" fill="#fff"/></svg></div><h3>Renters Insurance</h3><p>Protect personal belongings in a rental space, covering damage, theft, or loss due to disasters.</p></div>
<div class="card" style="left:868px;top:960px"><div class="icon"><svg width="30" height="30" viewBox="0 0 30 30"><rect x="8" y="4" width="14" height="22" fill="#0c2c77"/><path d="M11 8h2M17 8h2M11 12h2M17 12h2M11 16h2M17 16h2" stroke="#fff" stroke-width="2"/></svg></div><h3>Condo Insurance</h3><p>Cover your condo unit and personal property, filling the gap not covered by the building's insurance.</p></div>

<div class="card" style="left:84px;top:1209px"><div class="icon"><svg width="30" height="30" viewBox="0 0 30 30"><path d="M6 14L15 6l9 8v7H6z" fill="#0c2c77"/><path d="M3 24q3-3 6 0t6 0 6 0 6 0" stroke="#0c2c77" stroke-width="2" fill="none"/></svg></div><h3>Flood Insurance</h3><p>Provide financial protection against water damage caused by floods, which are often excluded from standard coverage.</p></div>
<div class="card" style="left:345px;top:1209px"><div class="icon"><svg width="30" height="30" viewBox="0 0 30 30"><circle cx="14" cy="6" r="2.5" fill="#0c2c77"/><path d="M14 10v7h6l3 6" stroke="#0c2c77" stroke-width="2.4" fill="none"/><path d="M10 14a6 6 0 1010 6" stroke="#0c2c77" stroke-width="2" fill="none"/></svg></div><h3>Disability Insurance</h3><p>Receive income replacement if you're unable to work due to illness or injury, ensuring financial security.</p></div>
<div class="card" style="left:607px;top:1209px"><div class="icon"><svg width="30" height="30" viewBox="0 0 30 30"><path d="M15 25S4 18 4 11a5.5 5.5 0 0111-2 5.5 5.5 0 0111 2c0 7-11 14-11 14z" fill="#0c2c77"/><path d="M15 11v8M11 15h8" stroke="#fff" stroke-width="2.2"/></svg></div><h3>Life Insurance</h3><p>Protect your loved ones financially after your passing, covering funeral expenses and ongoing living costs.</p></div>
<div class="card" style="left:868px;top:1209px"><div class="icon"><svg width="30" height="30" viewBox="0 0 30 30"><path d="M15 4l9 4v6c0 6-4 10-9 12-5-2-9-6-9-12V8z" fill="#0c2c77"/><path d="M15 10v8M11 14h8" stroke="#fff" stroke-width="2.2"/></svg></div><h3>Health Insurance</h3><p>Cover medical expenses, from check-ups to emergencies, ensuring you get the care you need without financial strain.</p></div>

<a class="btn btn-green" style="left:532px;top:1465px;width:134px;height:41px">Explore All</a>

<!-- About -->
<section class="about">
  <div class="eyebrow" style="left:615px;top:95px">Who We Are</div>
  <h2 class="heading" style="left:615px;top:124px;font-size:28px;line-height:40px">About Brellow Cover<br>Insurance</h2>
  <div class="rule" style="left:615px;top:212px"></div>
  <p style="top:245px">At Brellow Cover Insurance, we're dedicated to providing you with reliable, comprehensive insurance solutions tailored to your needs. Our mission is simple: to offer you peace of mind with the protection you deserve. We specialize in home, auto, health, and life insurance, and our experienced team is committed to helping you find the right coverage for every stage of life.</p>
  <p style="top:385px">Founded with a focus on customer satisfaction, Brellow Cover Insurance has grown to become a trusted partner in securing what matters most.</p>
  <a class="btn btn-green" style="left:615px;top:458px;width:139px;height:42px">Learn More</a>
</section>
<div class="photo" style="left:141px;top:1668px;width:294px;height:348px;background:linear-gradient(135deg,#a9acb2,#6e6a66 60%,#3d3b3a)" role="img" aria-label="Photo of an agent meeting a young couple at their front door"></div>
<div class="photo" style="left:242px;top:1908px;width:301px;height:212px;background:var(--white);box-shadow:0 3px 14px rgba(0,0,0,.1)"></div>
<div class="photo" style="left:252px;top:1916px;width:281px;height:196px;background:linear-gradient(180deg,#f1eeea,#e0c4ad 70%,#c9a186)" role="img" aria-label="Photo of hands holding a small model house"></div>

<!-- Partners -->
<section class="partners" role="region" aria-label="Partner carriers">
  <div class="eyebrow center" style="top:71px;color:var(--green)">Our Partners</div>
  <h2 class="center abs" style="top:100px;font-size:29px;font-weight:600;color:var(--white)">Trusted Partners for Your Protection</h2>
  <div class="rule" style="left:569px;top:141px"></div>
  <div class="logo-tile" style="left:-70px">Varnix</div>
  <div class="logo-tile" style="left:161px">Ostle</div>
  <div class="logo-tile" style="left:391px">Meridale Mutual</div>
  <div class="logo-tile" style="left:622px">Quillor</div>
  <div class="logo-tile" style="left:853px">Dunmarrow</div>
  <div class="logo-tile" style="left:1083px">Pellwick</div>
</section>

<!-- Testimonials -->
<div class="eyebrow center" style="top:2602px">Clients Testimonials</div>
<h2 class="heading center" style="top:2628px;font-size:29px">Proven Success Stories</h2>
<div class="rule" style="left:569px;top:2674px"></div>

<div class="quote-card" style="left:141px">
  <div class="mark">&ldquo;</div>
  <p>It is a long established fact that a reader will be distracted by the readable content of a page when looking at its layout. The point of using Lorem Ipsum is that it has a more-or-less normal distribution of letters, as opposed to using 'Content here, content here'.</p>
  <div class="avatar" style="left:116px" role="img" aria-label="Client portrait"></div>
  <div class="who" style="left:184px">Dorian Hale</div>
  <div class="stars" style="left:184px">★★★★★</div>
</div>
<div class="quote-card" style="left:613px">
  <div class="mark">&ldquo;</div>
  <p>It is a long established fact that a reader will be distracted by the readable content of a page when looking at its layout. The point of using Lorem Ipsum is that it has a more-or-less normal distribution of letters, as opposed to using 'Content here, content here'.</p>
  <div class="avatar" style="left:120px" role="img" aria-label="Client portrait"></div>
  <div class="who" style="left:192px">Tessa Marlowe</div>
  <div class="stars" style="left:192px">★★★★★</div>
</div>
<div class="arrow" style="left:125px;background:var(--white);border:1px solid #e3e6eb"><svg width="14" height="14" viewBox="0 0 14 14"><path d="M12 7H2M6 3L2 7l4 4" stroke="#8bc34a" stroke-width="1.6" fill="none"/></svg></div>
<div class="arrow" style="left:1043px;background:var(--green)"><svg width="14" height="14" viewBox="0 0 14 14"><path d="M2 7h10M8 3l4 4-4 4" stroke="#fff" stroke-width="1.6" fill="none"/></svg></div>
<div class="pager">
  <span style="left:555px"></span><span style="left:574px"></span>
  <span style="left:592px;top:3004px;width:15px;height:15px;background:var(--navy)"></span>
  <span style="left:617px"></span><span style="left:636px"></span>
</div>

<!-- Contact -->
<section class="contact">
  <div class="eyebrow" style="left:141px;top:92px">Contact Us</div>
  <h2 class="heading" style="left:141px;top:116px;font-size:28px">Get in Touch with Us</h2>
  <div class="rule" style="left:141px;top:158px"></div>
  <div class="field" style="left:141px;top:203px;width:227px;height:41px">First Name</div>
  <div class="field" style="left:387px;top:203px;width:228px;height:41px">Last Name</div>
  <div class="field" style="left:141px;top:265px;width:227px;height:41px">Email</div>
  <div class="field" style="left:387px;top:265px;width:228px;height:41px">Phone</div>
  <div class="field" style="left:141px;top:327px;width:474px;height:120px">Message</div>
  <a class="btn btn-green" style="left:141px;top:491px;width:147px;height:41px">Submit Now</a>
  <div class="photo" style="left:680px;top:72px;width:378px;height:474px;border-radius:14px;background:linear-gradient(135deg,#b9c4cf,#7d8a99 55%,#3f4b5b)" role="img" aria-label="Photo of a client and agent reviewing documents in a bright office"></div>
</section>

<!-- Footer -->
<footer class="footer">
  <div class="abs" style="left:141px;top:220px;display:flex;align-items:center;gap:8px;color:var(--white)">
    <span style="width:22px;height:22px;background:var(--green);display:block"></span>
    <span style="font-size:13px;font-weight:600;line-height:15px">BRELLOW COVER<br>INSURANCE</span>
  </div>
  <p class="abs" style="left:341px;top:219px;width:510px;font-size:11px;line-height:21px;color:#e1e8f5">Brellow Cover Insurance, we're dedicated to providing you with reliable, comprehensive insurance solutions tailored to your needs.</p>
  <div class="fsoc" style="left:926px;top:214px;background:var(--white)" aria-label="Social profile"></div>
  <div class="fsoc" style="left:974px;top:214px;background:var(--green)" aria-label="Social profile"></div>
  <div class="fsoc" style="left:1023px;top:214px;background:var(--white)" aria-label="Social profile"></div>
  <div class="abs" style="left:141px;top:281px;width:917px;height:1px;background:rgba(255,255,255,.25)"></div>
  <div class="abs center" style="top:318px;font-size:16px;font-weight:500;color:var(--white)">Contact Information</div>
  <div class="abs" style="left:141px;top:520px;width:917px;height:1px;background:rgba(255,255,255,.25)"></div>
  <div class="abs" style="left:141px;top:545px;font-size:12px;color:var(--white)">Copyright © 2025 Brellow Cover Insurance - All Rights Reserved.</div>
  <div class="abs" style="left:862px;top:545px;font-size:12px;color:var(--white)">Terms of use</div>
  <div class="abs" style="left:973px;top:545px;font-size:12px;color:var(--white)">Privacy Policy</div>
</footer>

<div class="fcol" style="left:151px"><svg width="20" height="20" viewBox="0 0 24 24"><path d="M6.6 10.8a15 15 0 006.6 6.6l2.2-2.2c.3-.3.7-.4 1-.2 1.1.4 2.3.6 3.6.6.6 0 1 .4 1 1V20c0 .6-.4 1-1 1C10.6 21 3 13.4 3 4c0-.6.4-1 1-1h3.5c.6 0 1 .4 1 1 0 1.3.2 2.5.6 3.6.1.3 0 .7-.2 1z" fill="#8bc34a"/></svg><h4>Call Us</h4><p>(555)-302-7781</p></div>
<div class="vline" style="left:399px"></div>
<div class="fcol" style="left:456px"><svg width="20" height="20" viewBox="0 0 24 24"><path d="M12 2a7 7 0 00-7 7c0 5 7 13 7 13s7-8 7-13a7 7 0 00-7-7z" fill="#8bc34a"/><circle cx="12" cy="9" r="2.6" fill="#0f4a9a"/></svg><h4>Find Us</h4><p>123, Lorem Ipsum is simply dummy<br>text of the printing</p></div>
<div class="vline" style="left:774px"></div>
<div class="fcol" style="left:788px"><svg width="22" height="20" viewBox="0 0 24 20"><rect x="1" y="2" width="22" height="16" rx="2" fill="#8bc34a"/><path d="M2 4l10 7 10-7" stroke="#0f4a9a" stroke-width="2" fill="none"/></svg><h4>Email Address</h4><p>info@brellowcover.com</p></div>

<div class="cta">
  <h2>Secure a Future with Customized Quote Today!</h2>
  <p>Protect what matters most with tailored insurance solutions. Get a personalized quote today and secure peace of mind.</p>
  <a class="btn" style="left:352px;top:189px;width:214px;height:43px;background:var(--white);color:var(--navy)">Get a Quote</a>
</div>

</body>
</html>
```